Business Cards for company that supports physicians that do medical research

Need to create a business card for Qorvel Studies (www.qorvelstudies.example), a company devoted to supporting physicians who conduct medical research. The form of the card should match the message of research and information quest. I have provided the logo of the company as an uploaded file. Designs should be simple and slick aimed at very high end clients.

Target Market(s)

Medical doctors that are also researchers

Industry/Entity Type

Medical

Contact Information for Business Card

Should feature logo and fields for personal info:
Name/title
Phone /email

Font styles to use
Serif
Sans Serif

Requirements
Must have
• Qorvel logo and fields for personal info:
• Name: Bertrand Okonfu
• Title: VP Research and Senior Analyst
• Phone: 555-203-4719
• email: info@qorvelstudies.example
Nice to have
• Interesting cards that I've seen:
• 1- all black/charcoal or very dark background
• 2- Plastic - semi-transparent
• 3- non-standard height-width ratios
• 4- Functional cards -- USB drive incorporated
Should not have
• Too busy; needs to stay very simple

```html
<!DOCTYPE html>
<html lang="en">
<head>
<meta charset="utf-8">
<title>Qorvel Studies — Business Card</title>
<link rel="stylesheet" href="https://fonts.googleapis.com/css2?family=Source+Sans+3:wght@400;600&display=swap">
<style>
  :root {
    --backdrop: #ecebe8;
    --card-dark: #000000;
    --brand-green: #6cc24a;
    --green-top: #6fc15f;
    --green-bottom: #52b645;
    --text-light: #ffffff;
    --shadow: rgba(0, 0, 0, 0.18);
  }
  * { margin: 0; padding: 0; box-sizing: border-box; }
  html, body {
    width: 1200px;
    height: 900px;
    overflow: hidden;
    background: var(--backdrop);
    font-family: "Source Sans 3", "Myriad Pro", Arial, sans-serif;
  }
  .canvas { position: relative; width: 1200px; height: 900px; }

  .card {
    position: absolute;
    width: 556px;
    height: 343px;
    box-shadow: 0 6px 18px var(--shadow);
  }

  /* Front side */
  .card--front { left: 238px; top: 62px; background: var(--card-dark); }
  .card--front .wordmark {
    position: absolute;
    left: 48px;
    top: 58px;
    font-size: 40px;
    font-weight: 600;
    color: var(--brand-green);
    letter-spacing: 0.5px;
    line-height: 1;
  }
  .person { position: absolute; left: 230px; top: 180px; color: var(--text-light); }
  .person__name {
    font-size: 21px;
    font-weight: 600;
    color: var(--brand-green);
    line-height: 1;
  }
  .person__title { margin-top: 10px; font-size: 15px; font-weight: 400; line-height: 1; }
  .contact { list-style: none; margin-top: 26px; }
  .contact__item {
    display: flex;
    align-items: center;
    gap: 10px;
    font-size: 15px;
    line-height: 1;
    height: 24px;
  }
  .contact__icon { width: 16px; height: 16px; flex: none; }

  /* Back side */
  .card--back {
    left: 458px;
    top: 518px;
    width: 559px;
    height: 342px;
    background: linear-gradient(180deg, var(--green-top), var(--green-bottom));
    display: flex;
    align-items: center;
    justify-content: center;
  }
  .card--back .wordmark {
    font-size: 48px;
    font-weight: 600;
    color: var(--text-light);
    letter-spacing: 0.5px;
    line-height: 1;
  }
</style>
</head>
<body>
<main class="canvas">
  <section class="card card--front" aria-label="Card front">
    <div class="wordmark">Qorvel Studies</div>
    <div class="person">
      <p class="person__name">Bertrand Okonfu</p>
      <p class="person__title">VP Research and Senior Analyst</p>
      <ul class="contact">
        <li class="contact__item">
          <svg class="contact__icon" viewBox="0 0 16 16" aria-hidden="true">
            <rect width="16" height="16" rx="2" fill="#6cc24a"/>
            <path d="M4 10.5 C4 9 5 8.5 8 8.5 C11 8.5 12 9 12 10.5 L12 11.5 L4 11.5 Z" fill="#fff"/>
            <rect x="3.5" y="5" width="9" height="2" rx="1" fill="#fff"/>
          </svg>
          <span>555-203-4719</span>
        </li>
        <li class="contact__item">
          <svg class="contact__icon" viewBox="0 0 16 16" aria-hidden="true">
            <rect width="16" height="16" rx="2" fill="#6cc24a"/>
            <rect x="3.5" y="5" width="9" height="6.5" fill="#fff"/>
            <path d="M3.5 5 L8 8.6 L12.5 5" fill="none" stroke="#6cc24a" stroke-width="1"/>
          </svg>
          <span>info@qorvelstudies.example</span>
        </li>
      </ul>
    </div>
  </section>

  <section class="card card--back" aria-label="Card back">
    <div class="wordmark">Qorvel Studies</div>
  </section>
</main>
</body>
</html>
```